Guitar parts retail packaging

I have 2 boxes I need designed. This will be for my guitar parts. They are going to be thick cardstock type paper box, with a foam insert to secure the items. Matte finish with silver foil printing is sort of where im headed, but Im open to other beautiful design. The boxes will need to have a window on top of the box to show the product inside. Color scheme Im thinking with is Black with red, white and Silver foil printing. Unless you come up with something nicer, im open to that. But my business cards and some stickers are those colors.
2 different size boxes, but they can be the same basic design, modified for 2 different sizes. They will open at the front, and the lid will lift, hinged at the top back edge. (Please see purple box in picture for example for how box will work). Both boxes will have a window on top to showcase product in the box. One of the sides, (2" X 1.25") will be left a solid color, grey or other so I can put a product sticker on that side to designate what type of product is in the box. So you are really just designing the top (With window), front, back, and 1 side. Maybe something clever on the bottom but if thats blank thats fine.
LARGE BOX:
5.25 wide (Left to right)
2” deep (Front to back)
1.25” tall (Top to bottom)
SMALL BOX:
2” Wide (Left to right)
2” Deep (Front to back)
Please see Business card and sticker in picture for color scheme Im thinking. ( I am open to other colors and designs as well)

Target Market(s)

Musicians, Rockers, tattoo junkies, general badasses.

Industry/Entity Type

Guitar industry. Rock & Rollers

Font styles to use
Other font styles liked:
• I use a font called Morpheus for my logo. Also Times New Roman, maybe Copperplate? Or something more creative? Im open as long as it fits.

Colors
EB3D1F
EC4F4E
F09395
F8D3D4
FCEDEE

Requirements
Must have
• My Company name and logo (Brackenmoor Goods). Also slogan-
Nice to have
• Please see general aesthetic in sticker and biz card.
Should not have
• No horror themes, keep it cool and classy. (Even though logo is a skull). And please no pictures of guitars on the box. You might add a pic of 1 type of guitar, but the parts inside might not fit that guitar pictured on the box.

```html
<!DOCTYPE html>
<html lang="en">
<head>
<meta charset="utf-8">
<title>Brackenmoor Goods – Long Box Lid</title>
<link rel="stylesheet" href="https://fonts.googleapis.com/css2?family=Metamorphous&display=swap">
<style>
  :root {
    --backdrop: #d4d4d4;
    --band-black: #121212;
    --band-black-soft: #2a2a2a;
    --lid-red: #9e1612;
    --lid-red-deep: #6f0d0b;
    --lid-red-bright: #b71c16;
    --panel-white: #f2f2f2;
    --panel-white-shade: #e0e0e0;
    --window-fill: #eeeeee;
    --window-edge: #c9c9c9;
    --ink-light: #f4f4f4;
    --ink-silver: #cfcfcf;
  }
  html, body {
    margin: 0;
    padding: 0;
    width: 1200px;
    height: 882px;
    overflow: hidden;
    background: var(--backdrop);
  }
  .canvas {
    position: relative;
    width: 1200px;
    height: 882px;
    font-family: "Metamorphous", "Times New Roman", serif;
  }
  .lid {
    position: absolute;
    left: 100px;
    top: 231px;
    width: 1000px;
    height: 420px;
    box-shadow: 0 18px 40px rgba(0,0,0,0.18);
  }
  .side-band {
    position: absolute;
    left: 0; top: 0;
    width: 1000px; height: 120px;
    background: radial-gradient(ellipse at 50% 50%, var(--band-black-soft), var(--band-black) 70%);
    display: flex;
    flex-direction: column;
    align-items: center;
    justify-content: center;
  }
  .side-band .brand-name {
    color: var(--ink-light);
    font-size: 40px;
    letter-spacing: 2px;
    line-height: 1;
    white-space: nowrap;
  }
  .side-band .slogan {
    color: var(--ink-silver);
    font-size: 18px;
    letter-spacing: 3px;
    margin-top: 8px;
    white-space: nowrap;
  }
  .front-face {
    position: absolute;
    left: 0; top: 120px;
    width: 1000px; height: 300px;
  }
  .red-field {
    position: absolute;
    left: 0; top: 0;
    width: 640px; height: 300px;
    background: radial-gradient(ellipse at 45% 45%, var(--lid-red-bright), var(--lid-red) 55%, var(--lid-red-deep));
  }
  .white-field {
    position: absolute;
    left: 640px; top: 0;
    width: 360px; height: 300px;
    background: linear-gradient(160deg, var(--panel-white), var(--panel-white-shade));
  }
  .thumb-notch {
    position: absolute;
    left: 0; top: 0;
  }
  .product-window {
    position: absolute;
    left: 660px; top: 75px;
    width: 320px; height: 180px;
    background: var(--window-fill);
    border: 2px solid var(--window-edge);
    border-radius: 30px;
    box-sizing: border-box;
  }
  .brand-lockup {
    position: absolute;
    left: 0; top: 0;
    width: 640px; height: 300px;
    display: flex;
    flex-direction: column;
    align-items: center;
    justify-content: center;
  }
  .brand-lockup .brand-mark {
    width: 34px; height: 34px;
    border-radius: 50%;
    border: 2px solid var(--ink-light);
    margin-bottom: 16px;
  }
  .brand-lockup .brand-name {
    color: var(--ink-light);
    font-size: 46px;
    letter-spacing: 2px;
    line-height: 1;
    white-space: nowrap;
  }
  .brand-lockup .slogan {
    color: var(--ink-light);
    font-size: 22px;
    letter-spacing: 3px;
    margin-top: 14px;
    white-space: nowrap;
  }
</style>
</head>
<body>
<div class="canvas">
  <div class="lid">
    <div class="side-band" role="img" aria-label="Black band with a dark damask pattern">
      <div class="brand-name">Brackenmoor Goods</div>
      <div class="slogan">STRUNG &amp; SWORN CRAFT</div>
    </div>
    <div class="front-face">
      <div class="red-field" role="img" aria-label="Deep red panel with a tonal damask pattern"></div>
      <div class="white-field" role="img" aria-label="White panel with a pale grey damask pattern"></div>
      <svg class="thumb-notch" width="1000" height="30" viewBox="0 0 1000 30" aria-hidden="true">
        <path d="M590 0 A22 22 0 0 0 634 0 Z" fill="var(--band-black)"/>
      </svg>
      <div class="product-window"></div>
      <div class="brand-lockup">
        <div class="brand-mark"></div>
        <div class="brand-name">Brackenmoor Goods</div>
        <div class="slogan">STRUNG &amp; SWORN CRAFT</div>
      </div>
    </div>
  </div>
</div>
</body>
</html>
```